Cover für Gedichtbuch
Zielgruppe
Das Buch soll jungen und alten Menschen gefallen. Zielgruppe sind aber vor allem junge Leser zwischen 18 und Mitte 20.
Aufgabenstellung
Für das Erstlingswerk von zwei Nachwuchsautoren wird ein Wendecover gesucht. Sprich: Auf der einen Seite stehen Gedichte mit hellen Gedichten (Liebe, Freude, Glück) - die andere Hälfte besteht aus dunklen Gedichten (Tod, Depression). Das Buch soll gedreht werden. Daher sollen die beiden Coverseiten einen Kontrast darstellen.

```html
<!DOCTYPE html>
<html lang="de">
<head>
<meta charset="utf-8">
<title>helle Gedichte – dunkle Gedichte</title>
<link rel="stylesheet" href="https://fonts.googleapis.com/css2?family=Cutive&display=swap">
<style>
  :root {
    --paper: #ffffff;
    --night: #000000;
    --ink-outline: #4a4a4a;
    --title-light: #ffffff;
    --title-silver: #d9d9d9;
  }
  html, body {
    margin: 0;
    padding: 0;
    width: 1200px;
    height: 845px;
    overflow: hidden;
    background: var(--paper);
  }
  .cover {
    display: block;
    width: 1200px;
    height: 845px;
  }
  .title {
    font-family: "Cutive", "Courier New", serif;
    stroke: var(--ink-outline);
    stroke-width: 1.5px;
  }
  .title--helle {
    font-size: 205px;
    fill: var(--title-light);
  }
  .title--gedi {
    font-size: 200px;
    fill: var(--title-light);
  }
  .title--chte {
    font-size: 195px;
    fill: url(#silver);
  }
  .title--dunkle {
    font-size: 135px;
    fill: var(--title-silver);
    stroke-width: 1.2px;
  }
</style>
</head>
<body>
<svg class="cover" viewBox="0 0 1200 845" xmlns="http://www.w3.org/2000/svg">
  <defs>
    <linearGradient id="light-side" x1="0" y1="0" x2="0" y2="1">
      <stop offset="0" stop-color="#ffffff"/>
      <stop offset="0.14" stop-color="#ffffff"/>
      <stop offset="0.25" stop-color="#b8712e"/>
      <stop offset="0.42" stop-color="#6b3f1c"/>
      <stop offset="0.62" stop-color="#8a5226"/>
      <stop offset="0.76" stop-color="#e7c9aa"/>
      <stop offset="0.86" stop-color="#ffffff"/>
    </linearGradient>
    <linearGradient id="dark-side" x1="0" y1="0" x2="0" y2="1">
      <stop offset="0" stop-color="#000000"/>
      <stop offset="0.05" stop-color="#000000"/>
      <stop offset="0.2" stop-color="#a9662a"/>
      <stop offset="0.5" stop-color="#c27a34"/>
      <stop offset="0.7" stop-color="#a86025"/>
      <stop offset="0.8" stop-color="#000000"/>
    </linearGradient>
    <linearGradient id="silver" x1="0" y1="1" x2="0" y2="0">
      <stop offset="0" stop-color="#ffffff"/>
      <stop offset="1" stop-color="#9a9a9a"/>
    </linearGradient>
    <filter id="title-shadow" x="-10%" y="-10%" width="120%" height="130%">
      <feDropShadow dx="2" dy="3" stdDeviation="3" flood-color="#000" flood-opacity="0.6"/>
    </filter>
  </defs>

  <rect class="side side--light" x="0" y="0" width="600" height="845" fill="url(#light-side)"
        role="img" aria-label="Baumkrone als Silhouette über alter Handschrift in Braun- und Orangetönen, oben und unten weiß verblassend"/>

  <rect class="side side--dark" x="607" y="0" width="593" height="845" fill="url(#dark-side)"
        role="img" aria-label="Wurzelwerk als dunkle Silhouette über kopfstehender alter Handschrift auf orangem Grund, oben und unten schwarz"/>

  <g filter="url(#title-shadow)">
    <text class="title title--helle" x="34" y="200" textLength="491" lengthAdjust="spacingAndGlyphs">helle</text>
    <text class="title title--gedi" x="139" y="471" textLength="445" lengthAdjust="spacingAndGlyphs">Gedi</text>
    <text class="title title--chte" x="618" y="-354" transform="scale(1,-1)" textLength="398" lengthAdjust="spacingAndGlyphs">chte</text>
    <text class="title title--dunkle" x="1168" y="690" transform="rotate(180 1168 690)" textLength="516" lengthAdjust="spacingAndGlyphs">dunkle</text>
  </g>
</svg>
</body>
</html>
```